NEW Modern Sleek Business Card for VR Language Startup

Our startup is using VR to lead the next wave of world language education. We need a two-sided business card that introduces the larger organization (Brightloom Language Inc) and our contact info on one side and shows the product, Glimwoorld, on the other side.

Side 1 (contact info)= Brightloom Logo and Contact info (name, title, phone, email)

Side 2 (product)= Glimworld logo, text, and website
Text= Culturally Immersive Language Learning Games
Website= www.glimworld-play.com

Target Market(s)

Education, Technology

Contact Information for Business Card

Contact info will be updated upon approval of the design. For now, put this as a placeholder.

Perry Dunmore
Founder & CEO
pdunmore@quillpost-mail.net
(555)-014-2286

Font styles to use
Other font styles liked:
• Gibson and Century Gothic are the brand fonts

Requirements
Nice to have
• I would love to see cohesion between the design and colors of the two logos. I have attached a few business card designs that I like, so you can get a feel for my preferred style.

```html
<!DOCTYPE html>
<html lang="en">
<head>
<meta charset="utf-8">
<title>Glimworld / Brightloom Language – Business Card</title>
<link rel="stylesheet" href="https://fonts.googleapis.com/css2?family=Montserrat:wght@400;500;600;700&family=Questrial&display=swap">
<style>
  :root {
    --page-bg: #e6e6e8;
    --card-black: #050505;
    --card-charcoal: #232323;
    --white: #ffffff;
    --grey-text: #4d4d4d;
    --product-blue: #4f7ef2;
    --tagline-violet: #6b4df2;
    --accent-red: #ee2a3a;
    --warm-orange: #f4a63a;
    --warm-red: #fb3640;
    --warm-magenta: #b0489e;
    --cool-cyan: #13e3ee;
    --cool-violet: #6a45f5;
  }
  * { box-sizing: border-box; margin: 0; padding: 0; }
  html, body {
    width: 1200px; height: 1200px; overflow: hidden;
    background: var(--page-bg);
  }
  .sheet {
    position: relative; width: 1200px; height: 1200px;
    display: flex; justify-content: center; align-items: center; gap: 102px;
  }
  .card {
    position: relative; width: 398px; height: 690px;
    border-radius: 44px; overflow: hidden;
    box-shadow: 0 10px 24px rgba(0,0,0,0.22);
    text-align: center;
  }

  /* Product side */
  .card--product {
    background: linear-gradient(160deg, var(--card-black) 30%, #111 100%);
  }
  .product-mark {
    position: absolute; left: 50%; top: 200px; transform: translateX(-50%);
    width: 130px; height: 130px; border-radius: 50%;
    background: var(--product-blue);
  }
  .product-name {
    position: absolute; left: 0; right: 0; top: 352px;
    font-family: "Montserrat", sans-serif; font-weight: 500;
    font-size: 46px; letter-spacing: 0.5px; color: var(--product-blue);
  }
  .product-tagline {
    position: absolute; left: 0; right: 0; top: 418px;
    font-family: "Questrial", sans-serif; font-size: 15.5px; line-height: 20px;
    color: var(--tagline-violet);
  }
  .product-website {
    position: absolute; left: 0; right: 0; top: 618px;
    font-family: "Montserrat", sans-serif; font-weight: 600;
    font-size: 14.5px; color: var(--grey-text);
  }

  /* Contact side */
  .card--contact {
    background: linear-gradient(160deg, #111 0%, var(--card-charcoal) 45%, #1a1a1a 100%);
  }
  .company-mark {
    position: absolute; left: 50%; top: 36px; transform: translateX(-50%);
    width: 108px; height: 108px; border-radius: 50%;
    background: var(--warm-red);
  }
  .company-name {
    position: absolute; left: 0; right: 0; top: 168px;
    font-family: "Montserrat", sans-serif; font-weight: 700;
    color: var(--white); line-height: 1;
  }
  .company-name__main { display: block; font-size: 33px; letter-spacing: 4px; }
  .company-name__sub { display: block; font-size: 19px; letter-spacing: 11px; margin-top: 14px; padding-left: 11px; }
  .person-name {
    position: absolute; left: 0; right: 0; top: 307px;
    font-family: "Montserrat", sans-serif; font-weight: 600;
    font-size: 23px; color: var(--white); letter-spacing: -0.3px;
  }
  .person-title {
    position: absolute; left: 0; right: 0; top: 340px;
    font-family: "Questrial", sans-serif; font-size: 15px; color: var(--white);
  }
  .divider {
    position: absolute; left: 50%; top: 368px; transform: translateX(-50%);
    width: 60px; height: 1.5px; background: var(--accent-red);
  }
  .contact-icons {
    position: absolute; left: 0; right: 0; top: 386px;
    display: flex; justify-content: center; gap: 10px;
  }
  .contact-icon { width: 17px; height: 17px; }
  .contact-line {
    position: absolute; left: 0; right: 0;
    font-family: "Questrial", sans-serif; color: var(--white);
  }
  .contact-line--phone { top: 411px; font-size: 15.5px; letter-spacing: 0.5px; }
  .contact-line--email { top: 436px; font-size: 14px; }
  .brand-corner {
    position: absolute; right: 0; bottom: 0; width: 230px; height: 220px;
    border-top-left-radius: 160px 200px;
    background: linear-gradient(180deg, var(--warm-orange) 0%, var(--warm-red) 55%, var(--warm-magenta) 100%);
  }
</style>
</head>
<body>
<main class="sheet">
  <section class="card card--product" aria-label="Product side">
    <div class="product-mark"></div>
    <h1 class="product-name">Glimworld</h1>
    <p class="product-tagline">Culturally Immersive Language<br>Learning Games</p>
    <p class="product-website">www.glimworld-play.com</p>
  </section>

  <section class="card card--contact" aria-label="Contact side">
    <div class="company-mark"></div>
    <h2 class="company-name">
      <span class="company-name__main">BRIGHTLOOM</span>
      <span class="company-name__sub">LANGUAGE</span>
    </h2>
    <p class="person-name">PERRY DUNMORE</p>
    <p class="person-title">Founder &amp; CEO</p>
    <div class="divider"></div>
    <div class="contact-icons">
      <svg class="contact-icon" viewBox="0 0 20 20" aria-label="Phone">
        <circle cx="10" cy="10" r="10" fill="#ee2a3a"/>
        <path d="M6.5 5.5l2 .3.6 2.2-1.2 1a6 6 0 0 0 2.9 2.9l1-1.2 2.2.6.3 2c-.2.6-1 1-1.8.9A8 8 0 0 1 5.6 7.3c-.1-.8.3-1.6.9-1.8z" fill="#fff"/>
      </svg>
      <svg class="contact-icon" viewBox="0 0 20 20" aria-label="Email">
        <circle cx="10" cy="10" r="10" fill="#ee2a3a"/>
        <rect x="5" y="6.5" width="10" height="7" rx="0.8" fill="#fff"/>
        <path d="M5.3 7l4.7 3.6L14.7 7" fill="none" stroke="#ee2a3a" stroke-width="1"/>
      </svg>
    </div>
    <p class="contact-line contact-line--phone">(555)-014-2286</p>
    <p class="contact-line contact-line--email">pdunmore@quillpost-mail.net</p>
    <div class="brand-corner" role="img" aria-label="Large warm-gradient brand decoration"></div>
  </section>
</main>
</body>
</html>
```